Packaging Design: Logo/Bottle Design for New Botanical Cocktail Brand

We are a new start up, looking to create a new line of Ready to drink Cocktails. The brand name is Verdance Garden Spritzers, infused with fruit, herb, and floral botanicals grown on our farm in New Hampshire. Flavors will include: Herb flavored with cilantro, Berry- flavored with Ridgeglow Berry, Citrus flavored with lemon Verbena & lemon balm, Pear flavored with Quillon pear, Cucumber & Mint. We need a logo and a label design. There are 2 possible bottles to choose from.

Designer has complete freedom with everything! From fonts and colors to bottle caps and closures. Please view the pinterest link for inspirational bottle designs. https://www.pinboardia.com/dellacravitz/garden-spritzers/

Reason: I am extending the deadline for my project to allow more designers to submit their designs.

Target Market(s)

Female 21 to 48 years old. College educated and professional. The type of person that has a passion for a cause and eats and shops local. People that respect an artisan quality product, hand made by a master craftsman.

Industry/Entity Type

Floral

Requirements
Must have
• Clear Bottle, see options attached. You may also choose your own BUT WE MUST SEE THE LOGO AND IMAGERY ON A BOTTLE
• Logo Design: "Verdance Garden Spritzers"
• Label: We can have front and back, or one continuous label. We are open to painted designs.
• The label must contain the following text in quotes:
• Product Name: " Verdance Garden Spritzers "
• "15% Alc. by Vol. (30 proof)"
• "750 mL"
• "Handcrafted and Bottled by Hollowmere Stillbrook Farm and Distillery
• Fernhollow, Ashmark-USA"
• The following Text must be in all caps and 3mm in height:
• "Government Warning: (1) According to the Surgeon General, women should not drink alcoholic beverages during pregnancy because of the risk of birth defects. (2) Consumption of alcoholic beverages impairs your ability to drive a car or operate machinery and may cause health problems."
• Must be a space for a bar code: .75 in height by 1.25 in length.
• “www.hollowmerestillbrook.com”
• Must Have the following Statement:
• Infused with fruit, herb, and floral botanicals and sweetened with stevia. Serve cold over ice.
Nice to have
• Antique or vintage botanical illustrations
• https://www.pinboardia.com/dellacravitz/garden-spritzers/
• check out the board for inspiration.
• Think artisanal small batch spirits that are ready to drink out of the bottle. Refreshing flavors just pour over ice and add herb leaves.
• You can use images by doing a search here.
• http://archv.plantrec.example.org/archv/search.xhtml?start=0&collectionFacet=Orchard+Painted+Plate+Archive

```html
<!DOCTYPE html>
<html lang="en">
<head>
<meta charset="utf-8">
<title>Verdance Garden Spritzers – Label Series</title>
<link href="https://fonts.googleapis.com/css2?family=Lora:ital,wght@0,400;0,600;0,700;1,400;1,600;1,700&display=swap" rel="stylesheet">
<style>
  :root {
    --page: #ffffff;
    --ink: #5f6149;
    --ink-soft: #8a8b74;
    --paper-light: #ece5d5;
    --paper-mid: #e0d6c1;
    --paper-dark: #cfc3aa;
    --panel: rgba(255, 255, 255, 0.55);
    --chip: #faf6f2;
    --warning-ink: #111111;
  }
  * { box-sizing: border-box; margin: 0; padding: 0; }
  html, body {
    width: 1200px; height: 1000px; overflow: hidden;
    background: var(--page);
    font-family: "Lora", Georgia, serif;
    color: var(--ink);
  }
  .sheet { position: relative; width: 1200px; height: 1000px; }

  .label {
    position: absolute;
    overflow: hidden;
    background:
      radial-gradient(ellipse at 30% 20%, rgba(255,255,255,0.35), transparent 60%),
      radial-gradient(ellipse at 80% 90%, rgba(160,140,105,0.18), transparent 55%),
      linear-gradient(160deg, var(--paper-light), var(--paper-mid) 55%, var(--paper-dark));
  }
  .label--berry    { left: 8px;   top: 14px;  width: 585px; height: 377px; }
  .label--herb     { left: 607px; top: 14px;  width: 585px; height: 377px; }
  .label--citrus   { left: 14px;  top: 628px; width: 571px; height: 369px; }
  .label--cucumber { left: 609px; top: 628px; width: 571px; height: 369px; }

  .label__art {
    position: absolute; left: 22%; top: 38%; width: 60%; height: 60%;
    border-radius: 50%;
    filter: blur(14px);
    opacity: 0.75;
  }
  .label--berry .label__art {
    background: radial-gradient(circle at 35% 45%, #f0a2a2 0%, #e9b1ad 30%, transparent 60%),
                radial-gradient(circle at 70% 55%, #eaa6a3 0%, transparent 45%),
                radial-gradient(circle at 45% 80%, #8d96b2 0%, transparent 40%);
  }
  .label--herb .label__art {
    left: 18%; top: 22%; width: 70%; height: 78%;
    background: radial-gradient(ellipse at 50% 50%, #a9cf8f 0%, #bcd9a3 40%, transparent 70%);
  }
  .label--citrus .label__art {
    left: 22%; top: 28%; width: 55%; height: 72%;
    background: radial-gradient(circle at 40% 30%, #f1e27d 0%, transparent 40%),
                radial-gradient(ellipse at 45% 75%, #8fb06d 0%, #b6c98f 35%, transparent 65%);
  }
  .label--cucumber .label__art {
    left: 30%; top: 40%; width: 55%; height: 55%;
    background: radial-gradient(ellipse at 50% 50%, #b9cf8c 0%, #cfdca8 40%, transparent 70%);
  }

  .brand-mark {
    position: absolute; left: 50%; transform: translateX(-50%);
    font-family: "Lora", Georgia, serif; font-weight: 600; color: var(--ink);
    white-space: nowrap; letter-spacing: 0.04em;
  }
  .brand-mark--main { top: 80px; font-size: 38px; }
  .brand-mark--corner { top: 52px; font-size: 11px; transform: none; }
  .brand-mark--corner-left { left: 5%; }
  .brand-mark--corner-right { left: auto; right: 5%; }

  .side-panel { position: absolute; background: var(--panel); }
  .side-panel--left  { left: 3.5%; top: 27%; width: 17.5%; height: 59%; }
  .side-panel--right { right: 3%; top: 30%; width: 18%; height: 54%; }

  .maker-note {
    position: absolute; left: 3.5%; top: 70%; width: 17.5%;
    font-size: 6.5px; line-height: 1.2; font-style: italic; text-align: center;
    color: var(--ink-soft);
  }
  .barcode-space {
    position: absolute; left: 5%; bottom: 4%; width: 12.5%; height: 9.5%;
    background: var(--chip);
    display: flex; align-items: center; justify-content: center;
    font-style: italic; font-size: 15px; color: var(--ink);
  }
  .serve-note {
    position: absolute; right: 3.5%; top: 25%;
    font-style: italic; font-size: 11px; color: var(--ink);
  }
  .gov-warning {
    position: absolute; right: 2%; bottom: 4%; width: 18.5%;
    background: #fff; border: 1px solid #333;
    padding: 3px 4px;
    font-family: Arial, Helvetica, sans-serif; font-size: 4.2px; line-height: 1.25;
    font-weight: 700; text-transform: uppercase; color: var(--warning-ink);
  }

  .flavor {
    position: absolute; left: 50%; transform: translateX(-50%);
    text-align: center; color: var(--ink); width: 46%;
  }
  .flavor__name { font-size: 44px; line-height: 1; font-weight: 700; font-style: italic; }
  .flavor__desc { font-size: 15px; line-height: 0.95; margin-top: 1px; }
  .label--berry .flavor, .label--herb .flavor { top: 58%; }
  .label--citrus .flavor { top: 55%; }
  .label--cucumber .flavor { top: 57%; }
  .label--berry .flavor { left: 51%; }

  .infusion-note {
    position: absolute; left: 50%; transform: translateX(-50%);
    top: 86%; width: 44%; text-align: center;
    font-style: italic; font-size: 9.5px; line-height: 1.2;
  }
  .volume-line {
    position: absolute; left: 50%; transform: translateX(-50%);
    bottom: 3%; font-size: 6.5px; letter-spacing: 0.04em; white-space: nowrap;
  }
  .volume-line span + span { margin-left: 26px; }

  .centre-mark {
    position: absolute; left: 600px; top: 510px; transform: translate(-50%, -50%);
    font-family: "Lora", Georgia, serif; font-weight: 600; font-size: 46px;
    letter-spacing: 0.04em; color: var(--ink);
  }
</style>
</head>
<body>
<main class="sheet">

  <section class="label label--berry">
    <div class="label__art" role="img" aria-label="Soft watercolour of ridgeglow berries and blueberries"></div>
    <div class="brand-mark brand-mark--corner brand-mark--corner-left">Verdance</div>
    <div class="brand-mark brand-mark--corner brand-mark--corner-right">Verdance</div>
    <div class="brand-mark brand-mark--main">Verdance</div>
    <div class="side-panel side-panel--left"></div>
    <div class="side-panel side-panel--right"></div>
    <p class="maker-note">Verdance Garden Spritzers<br>Handcrafted and Bottled<br>by Hollowmere<br>Stillbrook Farm<br>and Distillery<br>Fernhollow, Ashmark-USA</p>
    <div class="barcode-space">barcode</div>
    <p class="serve-note">Serve cold over ice.</p>
    <div class="flavor">
      <h2 class="flavor__name">Berry</h2>
      <p class="flavor__desc">flavored with<br>ridgeglow berries</p>
    </div>
    <p class="infusion-note">Infused with fruit, herb and floral<br>botanicals and sweetened with stevia.</p>
    <p class="volume-line"><span>750 ML</span><span>15% ALC. BY VOL. (30 PROOF)</span></p>
    <p class="gov-warning">Government Warning: (1) According to the Surgeon General, women should not drink alcoholic beverages during pregnancy because of the risk of birth defects. (2) Consumption of alcoholic beverages impairs your ability to drive a car or operate machinery, and may cause health problems.</p>
  </section>

  <section class="label label--herb">
    <div class="label__art" role="img" aria-label="Soft watercolour of fresh cilantro leaves"></div>
    <div class="brand-mark brand-mark--corner brand-mark--corner-left">Verdance</div>
    <div class="brand-mark brand-mark--corner brand-mark--corner-right">Verdance</div>
    <div class="brand-mark brand-mark--main">Verdance</div>
    <div class="side-panel side-panel--left"></div>
    <div class="side-panel side-panel--right"></div>
    <p class="maker-note">Verdance Garden Spritzers<br>Handcrafted and Bottled<br>by Hollowmere<br>Stillbrook Farm<br>and Distillery<br>Fernhollow, Ashmark-USA</p>
    <div class="barcode-space">barcode</div>
    <p class="serve-note">Serve cold over ice.</p>
    <div class="flavor">
      <h2 class="flavor__name">Herb</h2>
      <p class="flavor__desc">flavored<br>with<br>cilantro</p>
    </div>
    <p class="infusion-note">Infused with fruit, herb and floral<br>botanicals and sweetened with stevia.</p>
    <p class="volume-line"><span>750 ML</span><span>15% ALC. BY VOL. (30 PROOF)</span></p>
    <p class="gov-warning">Government Warning: (1) According to the Surgeon General, women should not drink alcoholic beverages during pregnancy because of the risk of birth defects. (2) Consumption of alcoholic beverages impairs your ability to drive a car or operate machinery, and may cause health problems.</p>
  </section>

  <div class="centre-mark">Verdance</div>

  <section class="label label--citrus">
    <div class="label__art" role="img" aria-label="Soft watercolour of lemon balm and lemon verbena with a yellow blossom"></div>
    <div class="brand-mark brand-mark--corner brand-mark--corner-left">Verdance</div>
    <div class="brand-mark brand-mark--corner brand-mark--corner-right">Verdance</div>
    <div class="brand-mark brand-mark--main">Verdance</div>
    <div class="side-panel side-panel--left"></div>
    <div class="side-panel side-panel--right"></div>
    <p class="maker-note">Verdance Garden Spritzers<br>Handcrafted and Bottled<br>by Hollowmere<br>Stillbrook Farm<br>and Distillery<br>Fernhollow, Ashmark-USA</p>
    <div class="barcode-space">barcode</div>
    <p class="serve-note">Serve cold over ice.</p>
    <div class="flavor">
      <h2 class="flavor__name">Citrus</h2>
      <p class="flavor__desc">with<br>lemon balm<br>and<br>lemon verbena</p>
    </div>
    <p class="infusion-note">Infused with fruit, herb and floral<br>botanicals and sweetened with stevia.</p>
    <p class="volume-line"><span>750 ML</span><span>15% ALC. BY VOL. (30 PROOF)</span></p>
    <p class="gov-warning">Government Warning: (1) According to the Surgeon General, women should not drink alcoholic beverages during pregnancy because of the risk of birth defects. (2) Consumption of alcoholic beverages impairs your ability to drive a car or operate machinery, and may cause health problems.</p>
  </section>

  <section class="label label--cucumber">
    <div class="label__art" role="img" aria-label="Soft watercolour of sliced cucumber and mint"></div>
    <div class="brand-mark brand-mark--corner brand-mark--corner-left">Verdance</div>
    <div class="brand-mark brand-mark--corner brand-mark--corner-right">Verdance</div>
    <div class="brand-mark brand-mark--main">Verdance</div>
    <div class="side-panel side-panel--left"></div>
    <div class="side-panel side-panel--right"></div>
    <p class="maker-note">Verdance Garden Spritzers<br>Handcrafted and Bottled<br>by Hollowmere<br>Stillbrook Farm<br>and Distillery<br>Fernhollow, Ashmark-USA</p>
    <div class="barcode-space">barcode</div>
    <p class="serve-note">Serve cold over ice.</p>
    <div class="flavor">
      <h2 class="flavor__name">Cucumber</h2>
      <p class="flavor__desc">flavored<br>with<br>mint</p>
    </div>
    <p class="infusion-note">Infused with fruit, herb and floral<br>botanicals and sweetened with stevia.</p>
    <p class="volume-line"><span>750 ML</span><span>15% ALC. BY VOL. (30 PROOF)</span></p>
    <p class="gov-warning">Government Warning: (1) According to the Surgeon General, women should not drink alcoholic beverages during pregnancy because of the risk of birth defects. (2) Consumption of alcoholic beverages impairs your ability to drive a car or operate machinery, and may cause health problems.</p>
  </section>

</main>
</body>
</html>
```